MRT Property - Business Cards

Looking for a business card & general letterhead, signage etc design for our new logo.

Colours:
000a20
0056a2
00b5ef
0088ce
68cef2

Fonts:
Poppins
Karla

Please keep look and feel of new brand - example in the zip package I sent.

```html
<!DOCTYPE html>
<html lang="en">
<head>
<meta charset="utf-8">
<title>MRT Property – Stationery</title>
<link rel="stylesheet" href="https://fonts.googleapis.com/css2?family=Poppins:wght@400;500;600&display=swap">
<style>
  :root {
    --navy: #0e1428;
    --deep-blue: #0d56a6;
    --mid-blue: #0088ce;
    --sky-blue: #5ccbf2;
    --paper: #ffffff;
    --backdrop: #e2e2e2;
    --ink: #1b1f2a;
  }
  * { box-sizing: border-box; margin: 0; padding: 0; }
  html, body { width: 1200px; height: 686px; overflow: hidden; }
  body {
    background: var(--backdrop);
    font-family: "Poppins", sans-serif;
    position: relative;
  }

  /* Letterhead */
  .letterhead {
    position: absolute; left: 80px; top: 33px;
    width: 438px; height: 620px;
    background: var(--paper);
    box-shadow: 0 6px 18px rgba(0,0,0,.18);
    overflow: hidden;
  }
  .letterhead .brand-name {
    position: absolute; left: 40px; top: 46px;
    font-weight: 600; font-size: 26px; color: var(--deep-blue);
    letter-spacing: .5px;
  }
  .letterhead .contact-block {
    position: absolute; left: 248px; top: 118px;
    padding-left: 14px;
    border-left: 1.5px solid var(--mid-blue);
    font-size: 8.5px; line-height: 1.45; color: var(--ink);
  }
  .contact-row { display: flex; align-items: flex-start; gap: 5px; }
  .contact-row + .contact-row { margin-top: 2px; }
  .contact-row.address { margin-bottom: 6px; }
  .icon { width: 8px; height: 8px; flex: none; margin-top: 2px; }
  .letterhead .edge-band {
    position: absolute; left: 0; bottom: 0; width: 100%; height: 14px;
  }

  /* Business cards */
  .card {
    position: absolute; left: 640px;
    width: 440px; height: 256px;
    background: var(--navy);
    border-radius: 12px;
    overflow: hidden;
    box-shadow: 0 6px 18px rgba(0,0,0,.22);
    color: #fff;
  }
  .card-front { top: 40px; }
  .card-back { top: 380px; }
  .card .edge-band {
    position: absolute; left: 0; bottom: 0; width: 100%; height: 14px;
  }

  .card-front .brand-name {
    position: absolute; left: 36px; top: 62px;
    font-weight: 600; font-size: 25px; color: var(--deep-blue);
  }
  .card-front .divider {
    position: absolute; left: 220px; top: 40px;
    width: 1px; height: 140px; background: var(--deep-blue);
  }
  .card-front .person {
    position: absolute; left: 240px; top: 52px;
  }
  .person-name { font-weight: 500; font-size: 21px; color: var(--mid-blue); line-height: 1.1; }
  .person-role { font-size: 10px; color: #fff; margin-bottom: 12px; }
  .card-front .contact-row { font-size: 9px; color: #fff; line-height: 1.45; }
  .card-front .address-line {
    position: absolute; left: 24px; bottom: 24px;
    font-size: 9px; color: #fff;
  }

  .card-back .brand-name {
    position: absolute; left: 0; right: 0; top: 96px;
    text-align: center;
    font-weight: 600; font-size: 40px; color: var(--deep-blue);
  }
</style>
</head>
<body>

<section class="letterhead" aria-label="Letterhead">
  <div class="brand-name">MRT Property</div>

  <div class="contact-block">
    <div class="contact-row address">
      <svg class="icon" viewBox="0 0 10 10"><path d="M5 0.5a3.3 3.3 0 0 1 3.3 3.3C8.3 6.3 5 9.5 5 9.5S1.7 6.3 1.7 3.8A3.3 3.3 0 0 1 5 .5z" fill="#0088ce"/><circle cx="5" cy="3.8" r="1.2" fill="#fff"/></svg>
      <span>Suite 3.04, Level 2<br>18 Harbour Lane<br>Rhodes NSW 2138</span>
    </div>
    <div class="contact-row">
      <svg class="icon" viewBox="0 0 10 10"><path d="M2.2 1l1.8 2-1 1.2c.6 1.3 1.5 2.2 2.8 2.8l1.2-1 2 1.8-1.2 1.6C4.6 9.2.8 5.4.6 2.2z" fill="#0088ce"/></svg>
      <span>+61 2 9000 1234</span>
    </div>
    <div class="contact-row">
      <svg class="icon" viewBox="0 0 10 10"><circle cx="5" cy="5" r="4.2" fill="none" stroke="#0088ce" stroke-width="1"/><path d="M.8 5h8.4M5 .8c-2.2 2.4-2.2 6 0 8.4M5 .8c2.2 2.4 2.2 6 0 8.4" fill="none" stroke="#0088ce" stroke-width=".8"/></svg>
      <span>www.mrtproperty.com.au</span>
    </div>
    <div class="contact-row">
      <svg class="icon" viewBox="0 0 10 10"><rect x=".6" y="2" width="8.8" height="6.2" rx=".8" fill="#0088ce"/><path d="M1 2.4l4 3 4-3" fill="none" stroke="#fff" stroke-width=".8"/></svg>
      <span>info@mrtproperty.com.au</span>
    </div>
  </div>

  <svg class="edge-band" viewBox="0 0 438 14" preserveAspectRatio="none">
    <rect x="0" y="6" width="200" height="8" fill="var(--sky-blue)"/>
    <polygon points="186,0 438,0 438,14 200,14" fill="var(--deep-blue)"/>
  </svg>
</section>

<section class="card card-front" aria-label="Business card front">
  <div class="brand-name">MRT Property</div>
  <div class="divider"></div>
  <div class="person">
    <div class="person-name">Owen Hartley</div>
    <div class="person-role">Director</div>
    <div class="contact-row">
      <svg class="icon" viewBox="0 0 10 10"><path d="M2.2 1l1.8 2-1 1.2c.6 1.3 1.5 2.2 2.8 2.8l1.2-1 2 1.8-1.2 1.6C4.6 9.2.8 5.4.6 2.2z" fill="#5ccbf2"/></svg>
      <span>+61 2 9000 1234</span>
    </div>
    <div class="contact-row">
      <svg class="icon" viewBox="0 0 10 10"><circle cx="5" cy="5" r="4.2" fill="none" stroke="#5ccbf2" stroke-width="1"/><path d="M.8 5h8.4M5 .8c-2.2 2.4-2.2 6 0 8.4M5 .8c2.2 2.4 2.2 6 0 8.4" fill="none" stroke="#5ccbf2" stroke-width=".8"/></svg>
      <span>www.mrtproperty.com.au</span>
    </div>
    <div class="contact-row">
      <svg class="icon" viewBox="0 0 10 10"><rect x=".6" y="2" width="8.8" height="6.2" rx=".8" fill="#5ccbf2"/><path d="M1 2.4l4 3 4-3" fill="none" stroke="#0e1428" stroke-width=".8"/></svg>
      <span>info@mrtproperty.com.au</span>
    </div>
  </div>
  <div class="address-line">Suite 3.04, Level 2, 18 Harbour Lane, Rhodes NSW 2138</div>
  <svg class="edge-band" viewBox="0 0 440 14" preserveAspectRatio="none">
    <rect x="0" y="5" width="200" height="9" fill="var(--sky-blue)"/>
    <polygon points="186,0 440,0 440,14 200,14" fill="var(--deep-blue)"/>
  </svg>
</section>

<section class="card card-back" aria-label="Business card back">
  <div class="brand-name">MRT Property</div>
  <svg class="edge-band" viewBox="0 0 440 14" preserveAspectRatio="none">
    <rect x="0" y="5" width="200" height="9" fill="var(--sky-blue)"/>
    <polygon points="186,0 440,0 440,14 200,14" fill="var(--deep-blue)"/>
  </svg>
</section>

</body>
</html>
```